Dry Cleaners Pick-up & Delivery Service

We are in the need of a post card design to hand out in public focused in our dry-cleaners pick up and delivery business services. The postcard must include a price list of most common items sent to the dry cleaners on a regular basis along with promotional sign-up deals and specials as advertised on our website. The color palette must match our website's color scheme - www.tovrastik.com - we would like to focus on our free pick-up and free delivery service. The hand out post card should look clean, organized and neat, yet modern in style projecting the cleanliness of the clothing articles that our customer let us take care of saving them time while we take care of this errand for them. All new customers receive a free high quality, heavy duty laundry bag with our business information and are encouraged to request for $10 of free dry cleaning on their first order, no strings attached, just for signing up to our service.We strive to please our customers and invest on them to have more free time on their hands, plain and simple. We also offer law enforcement uniform special, as the area we focus our routes is a high law enforcement residential community. The logo is attached and must be visible in the postcard as well as the website address and phone number 305-471-2093 as these are the main contact forms of clients reaching our business. This is home based business, we have a partnership with a dry cleaners business who does all of our route customers' dry cleaning needs. Our business is all about the marketing, sales and networking with corporate businesses. The postcard handout must have designs of both sides of the post card as well. They will not be used for mailing for the moment being, they will be only used to hand out.

Industry/Entity Type

Dry Cleaning

```html
<!DOCTYPE html>
<html lang="en">
<head>
<meta charset="utf-8">
<title>Tovrastik Postcard – Front and Back</title>
<link rel="stylesheet" href="https://fonts.googleapis.com/css2?family=Audiowide&family=PT+Sans:wght@400;700&display=swap">
<style>
  :root {
    --green: #6cc04a;
    --green-dark: #3e9a2a;
    --ink: #141414;
    --panel: #2b2b2b;
    --paper: #ffffff;
    --stage: #2a2a2a;
    --shirt-light: #dfe8f1;
    --shirt-blue: #7f9fc6;
    --footer: #000000;
  }
  * { box-sizing: border-box; margin: 0; padding: 0; }
  html, body { width: 1200px; height: 1170px; overflow: hidden; }
  body {
    position: relative;
    background: var(--stage);
    font-family: "PT Sans", sans-serif;
    color: var(--ink);
  }
  .card {
    position: absolute;
    width: 695px;
    height: 540px;
    background: var(--paper);
    overflow: hidden;
  }
  .card--front { left: 56px; top: 59px; }
  .card--back { left: 404px; top: 618px; }

  .front-photo {
    position: absolute; inset: 0 0 60px 0;
    background:
      linear-gradient(180deg, rgba(255,255,255,1) 0%, rgba(255,255,255,0.85) 28%, rgba(255,255,255,0) 55%),
      linear-gradient(100deg, var(--shirt-light) 0%, #b9cbe0 35%, var(--shirt-blue) 60%, #c7d6e6 85%, var(--shirt-light) 100%);
  }

  .brand { position: absolute; text-align: center; }
  .brand__name {
    font-family: "Audiowide", sans-serif;
    color: var(--ink);
    line-height: 1;
  }
  .brand__tagline {
    font-family: "PT Sans", sans-serif;
    color: var(--ink);
    white-space: nowrap;
  }
  .card--front .brand { left: 0; right: 0; top: 60px; }
  .card--front .brand__name { font-size: 64px; }
  .card--front .brand__tagline { font-size: 24px; margin-top: 32px; }
  .card--back .brand { left: 40px; width: 270px; top: 44px; }
  .card--back .brand__name { font-size: 38px; }
  .card--back .brand__tagline { font-size: 14px; margin-top: 24px; }

  .cta { position: absolute; font-family: "Audiowide", sans-serif; text-align: center; border-radius: 3px; }
  .cta--signup { background: var(--panel); color: #fff; }
  .cta--signup .cta__url { color: var(--green); }
  .cta--call { background: var(--green); color: #fff; }
  .cta--call .cta__note { color: var(--ink); }

  .card--front .cta--signup { left: 178px; top: 219px; width: 366px; height: 74px; padding-top: 8px; font-size: 22px; line-height: 31px; }
  .card--front .cta--call { left: 178px; top: 295px; width: 366px; height: 74px; padding-top: 8px; font-size: 23px; line-height: 28px; }
  .card--front .cta--call .cta__note { font-size: 15px; line-height: 20px; }

  .card--back .cta--signup { left: 418px; top: 36px; width: 241px; height: 48px; padding-top: 5px; font-size: 15px; line-height: 20px; }
  .card--back .cta--call { left: 418px; top: 86px; width: 241px; height: 48px; padding-top: 5px; font-size: 15px; line-height: 20px; }
  .card--back .cta--call .cta__note { font-size: 10px; line-height: 14px; }

  .free-bubble { position: absolute; left: 510px; top: 300px; width: 150px; height: 150px; }
  .free-bubble__word {
    position: absolute; left: 537px; top: 330px;
    font-family: "Audiowide", sans-serif; font-size: 22px; color: var(--green);
  }
  .free-bubble__text {
    position: absolute; left: 574px; top: 362px;
    font-size: 14px; line-height: 17px; transform: rotate(-18deg);
  }
  .bag { position: absolute; background: linear-gradient(160deg, #5fbf46, #2f8a25); border-radius: 6px 6px 12px 12px; }
  .card--front .bag { left: 535px; top: 368px; width: 34px; height: 48px; }

  .seal { position: absolute; border-radius: 50%; background: var(--ink); box-shadow: 0 0 0 3px #fff inset, 0 0 0 5px var(--ink) inset; }
  .card--front .seal { left: 593px; top: 398px; width: 76px; height: 76px; }

  .offer {
    position: absolute; left: 184px; top: 405px; width: 380px;
    color: #fff; font-size: 21px; line-height: 27px; text-align: center;
    text-shadow: 0 1px 3px rgba(0,0,0,0.45);
  }
  .offer__badge {
    position: absolute; left: 0; top: 16px; width: 52px; height: 52px;
    border-radius: 50%; background: var(--green);
  }
  .offer__line { position: relative; }

  .contact-bar {
    position: absolute; left: 0; right: 0; bottom: 0; height: 60px;
    background: var(--footer); color: var(--green);
    font-size: 16px; line-height: 60px; text-align: center; white-space: nowrap;
  }
  .card--back .contact-bar { font-size: 17px; }

  .feature { position: absolute; left: 183px; width: 480px; }
  .feature__title { font-family: "Audiowide", sans-serif; color: var(--green); font-size: 16px; letter-spacing: 0.5px; margin-bottom: 7px; }
  .feature__body { font-size: 11px; line-height: 14.5px; color: var(--ink); }
  .feature--pickup { top: 178px; }
  .feature--service { top: 267px; }
  .feature--savings { top: 364px; }

  .feature-art--courier {
    position: absolute; left: 66px; top: 166px; width: 80px; height: 78px;
    background: linear-gradient(90deg, #e8eef5 0%, #c9d7e6 55%, #4fae3c 56%, #2f8a25 100%);
    border-radius: 8px;
  }
  .card--back .seal { left: 64px; top: 263px; width: 80px; height: 80px; }
  .dollar {
    position: absolute; left: 76px; top: 352px;
    font-family: "PT Sans", sans-serif; font-weight: 700; font-size: 90px; line-height: 1; color: var(--green);
  }
</style>
</head>
<body>

<section class="card card--front">
  <div class="front-photo" role="img" aria-label="Photograph of freshly cleaned dress shirts on hangers in light blue tones"></div>

  <div class="brand">
    <div class="brand__name">Tovrastik</div>
    <div class="brand__tagline">Dry Cleaners Pick-up &amp; Delivery Services, LLC</div>
  </div>

  <div class="cta cta--signup">
    <div>Sign-up free!</div>
    <div class="cta__url">www.tovrastik.com</div>
  </div>
  <div class="cta cta--call">
    <div>Call 305-471-2093</div>
    <div class="cta__note">next-day service available!</div>
  </div>

  <svg class="free-bubble" viewBox="0 0 150 150" aria-hidden="true">
    <circle cx="78" cy="75" r="66" fill="#9a9a9a"/>
    <path d="M8 40 L40 30 L30 60 Z" fill="#ffffff"/>
    <circle cx="74" cy="75" r="66" fill="#ffffff"/>
  </svg>
  <div class="free-bubble__word">FREE</div>
  <div class="bag" role="img" aria-label="Illustration of a green laundry bag"></div>
  <div class="free-bubble__text">Pick-Up<br>&amp; Delivery</div>
  <div class="seal" aria-hidden="true"></div>

  <div class="offer">
    <span class="offer__badge" aria-hidden="true"></span>
    <div class="offer__line">Ask about getting</div>
    <div class="offer__line">$10 off your first dry-cleaning order!</div>
  </div>

  <footer class="contact-bar">2270 NW 88th Ave Miami FL 33172 us &nbsp;|&nbsp; 305-471-2093 &nbsp;|&nbsp; deliveryservice@tovrastik.com</footer>
</section>

<section class="card card--back">
  <div class="brand">
    <div class="brand__name">Tovrastik</div>
    <div class="brand__tagline">Dry Cleaners Pick-up &amp; Delivery Services, LLC</div>
  </div>

  <div class="cta cta--signup">
    <div>Sign-up free!</div>
    <div class="cta__url">www.tovrastik.com</div>
  </div>
  <div class="cta cta--call">
    <div>Call 305-471-2093</div>
    <div class="cta__note">next-day service available!</div>
  </div>

  <div class="feature-art--courier" role="img" aria-label="Illustration of a delivery man holding folded laundry and a green laundry bag"></div>
  <div class="feature feature--pickup">
    <h2 class="feature__title">Free Pick-up &amp; Delivery Dry-cleaning</h2>
    <p class="feature__body">Our delivery service is FREE of charge, even if it is a next-day service request, all you pay is for your dry cleaning or laundry service.<br>No hidden delivery fees.</p>
  </div>

  <div class="seal" aria-hidden="true"></div>
  <div class="feature feature--service">
    <h2 class="feature__title">Fast dependable Service</h2>
    <p class="feature__body">You can rest assured that we will take good care of your items like they were ours!<br>Customer service is at the top of our list and satisfaction is guaranteed!</p>
  </div>

  <div class="dollar" aria-hidden="true">$</div>
  <div class="feature feature--savings">
    <h2 class="feature__title">Save time and Money</h2>
    <p class="feature__body">We know what it's like to have to deal with your daily errands in your daily life and how extended work hours come into play. Save the hassle of having to drop and pick-up your clothes and let us pamper you a little bit. Enjoy more your well deserved time-off with your family from now on!</p>
  </div>

  <footer class="contact-bar">2270 NW 88th Ave Miami FL 33172 us &nbsp;|&nbsp; 305-471-2093 &nbsp;|&nbsp; deliveryservice@tovrastik.com</footer>
</section>

</body>
</html>
```